Marwick Law Letterhead

We need a new letterhead design for a Law Firm. The address for the law firm is 1475 Calloway Street, Suite 210, Houston, Texas 77041. Phone Number: 832-361-9027; Fax Number: 832-614-7359. The logo is uploaded to the project.

```html
<!DOCTYPE html>
<html lang="en">
<head>
<meta charset="utf-8">
<title>Marwick Law Letterhead</title>
<link rel="stylesheet" href="https://fonts.googleapis.com/css2?family=Montserrat:wght@400;500;600&display=swap">
<style>
  :root {
    --navy: #1b3468;
    --red: #d71f28;
    --red-deep: #8e1219;
    --ink: #2c2c2c;
    --paper: #ffffff;
    --backdrop: #e9eaec;
  }
  * { box-sizing: border-box; margin: 0; padding: 0; }
  html, body {
    width: 1200px; height: 874px; overflow: hidden;
    background: var(--backdrop);
    font-family: "Montserrat", Arial, sans-serif;
    color: var(--ink);
  }
  .letterhead {
    position: absolute; left: 310px; top: 27px;
    width: 580px; height: 820px;
    background: var(--paper);
    box-shadow: 0 4px 18px rgba(0,0,0,0.12);
    overflow: hidden;
  }
  .brand {
    position: absolute; left: 56px; top: 58px;
    display: flex; align-items: center; gap: 12px;
  }
  .brand-mark {
    width: 26px; height: 26px; border-radius: 50%;
    background: var(--navy);
  }
  .brand-name {
    font-size: 30px; font-weight: 600; color: var(--navy);
    letter-spacing: 0.5px;
  }
  .letter {
    position: absolute; left: 56px; top: 240px; width: 440px;
    font-size: 10.5px; line-height: 1.5;
  }
  .recipient { margin-bottom: 10px; }
  .letter p { margin-bottom: 22px; }
  .closing { margin-top: -4px; }
  .signature {
    width: 130px; height: 58px; margin-top: 12px;
    background: linear-gradient(135deg, #f3f3f3, #e3e3e3);
    border-radius: 3px;
  }
  .footer {
    position: absolute; left: 0; bottom: 0; width: 580px; height: 78px;
  }
  .footer-bands { position: absolute; left: 0; top: 0; }
  .footer-address, .footer-contact {
    position: absolute; display: flex; align-items: center; gap: 6px;
    color: #fff; font-size: 11px; font-weight: 500;
    white-space: nowrap; line-height: 1;
  }
  .footer-address { left: 20px; top: 26px; height: 34px; }
  .footer-contact { right: 18px; top: 8px; height: 18px; gap: 14px; }
  .footer-contact span { display: flex; align-items: center; gap: 5px; }
  .icon { width: 11px; height: 11px; fill: #fff; flex-shrink: 0; display: block; }
</style>
</head>
<body>
  <main class="letterhead">
    <header class="brand">
      <div class="brand-mark"></div>
      <div class="brand-name">Marwick Law</div>
    </header>

    <section class="letter">
      <div class="recipient">
        Mr/s<br>First Name and Last Name<br>Company Name<br>Address
      </div>
      <p>Lorem Ipsum is simply dummy text of the printing and typesetting industry. Lorem Ipsum has been the industry's standard dummy text ever since the 1500s, when an unknown printer took a galley of type and scrambled it to make a type specimen book. It has survived not only five centuries, but also the leap into electronic typesetting, remaining essentially unchanged. It was popularised in the 1960s with the release of Letraset sheets containing Lorem Ipsum passages.</p>
      <p>he standard chunk of Lorem Ipsum used since the 1500s is reproduced below for those interested. Sections 1.10.32 and 1.10.33 from "de Finibus Bonorum et Malorum" by Cicero are also reproduced in their exact original form, accompanied by English versions from the 1914 translation by H. Rackham. Lorem ipsum dolor sit amet, consectetur adipiscing elit, sed do eiusmod tempor incididunt ut labore et dolore magna aliqua.</p>
      <p>It is a long established fact that a reader will be distracted by the readable content of a page when looking at its layout. The point of using Lorem Ipsum is that it has a more-or-less normal distribution of letters, as opposed to using 'Content here, content here', making it look like readable English. Many desktop publishing packages and web page editors now .</p>
      <div class="closing">Your Sincerely,</div>
      <div class="signature" role="img" aria-label="Handwritten signature"></div>
    </section>

    <footer class="footer">
      <svg class="footer-bands" viewBox="0 0 580 78" width="580" height="78" aria-hidden="true">
        <defs>
          <linearGradient id="redBand" x1="0" x2="1" y1="0" y2="0">
            <stop offset="0" stop-color="#8e1219"/>
            <stop offset="1" stop-color="#d71f28"/>
          </linearGradient>
        </defs>
        <polygon points="0,66 580,66 580,0 392,0 378,66" fill="#1b3468"/>
        <rect x="0" y="66" width="580" height="12" fill="#1b3468"/>
        <polygon points="0,26 374,26 362,60 0,60" fill="url(#redBand)"/>
      </svg>
      <div class="footer-address">
        <svg class="icon" viewBox="0 0 24 24" aria-hidden="true"><path d="M12 2a7 7 0 0 0-7 7c0 5 7 13 7 13s7-8 7-13a7 7 0 0 0-7-7zm0 9.5A2.5 2.5 0 1 1 12 6.5a2.5 2.5 0 0 1 0 5z"/></svg>
        <span>1475 Calloway Street, Suite 210, Houston, Texas 77041</span>
      </div>
      <div class="footer-contact">
        <span>
          <svg class="icon" viewBox="0 0 24 24" aria-hidden="true"><path d="M6.6 10.8a15 15 0 0 0 6.6 6.6l2.2-2.2a1 1 0 0 1 1-.25 11.4 11.4 0 0 0 3.6.57 1 1 0 0 1 1 1V20a1 1 0 0 1-1 1A17 17 0 0 1 3 4a1 1 0 0 1 1-1h3.5a1 1 0 0 1 1 1 11.4 11.4 0 0 0 .57 3.6 1 1 0 0 1-.25 1z"/></svg>
          832-361-9027
        </span>
        <span>
          <svg class="icon" viewBox="0 0 24 24" aria-hidden="true"><path d="M7 3h10v5H7zM4 9h16a1 1 0 0 1 1 1v8h-4v3H7v-3H3v-8a1 1 0 0 1 1-1zm5 7v3h6v-3z"/></svg>
          832-614-7359
        </span>
      </div>
    </footer>
  </main>
</body>
</html>
```